Automotive component supplier needs a business card design

We need a business card design for our company called Velran Global Components Ltd based in the UK. We are a supplier of interior and exterior components to premium car manufacturers such as Corvel Ashby, Hadley Fenn, Marquist and Tavarelli. We would like to see a modern business card design that uses the colour blue.

Target Market(s)

Premium automotive car manufacturers.

Industry/Entity Type

Automotive

Contact Information for Business Card

Company Name : Velran Global Components Limited
Address: 17 Marlow Yard, Upper Heath, Warwick, CV31 8QL, United Kingdom
Web Address : www.velrancomponents-example.co.uk

Font styles to use
Other font styles liked:
• Helvetica

Colors
3176b5
0255a3
85acd3
cfdeed
cee9f5
85cae6
34a6d7
0692cd
9bcb3c

Requirements
Must have
• Clear company logo and a mixture of blue colours.
Nice to have
• A high quality modern image.
Should not have
• Multiple colours.

```html
<!DOCTYPE html>
<html lang="en">
<head>
<meta charset="utf-8">
<title>Velran Global Components – Business Card</title>
<link rel="stylesheet" href="https://fonts.googleapis.com/css2?family=Lato:wght@400;700&display=swap">
<style>
  :root {
    --brand-blue: #0a8bcd;
    --deep-blue: #0255a3;
    --accent-green: #9bcb3c;
    --ink: #1e1e24;
    --paper: #ffffff;
    --backdrop: #e9edf1;
  }
  * { box-sizing: border-box; margin: 0; padding: 0; }
  html, body { width: 1200px; height: 800px; overflow: hidden; }
  body {
    background: var(--backdrop);
    font-family: "Lato", Helvetica, Arial, sans-serif;
    position: relative;
  }
  .card {
    position: absolute;
    width: 600px;
    height: 343px;
    border-radius: 4px;
    box-shadow: 0 6px 18px rgba(0, 0, 0, 0.18);
    overflow: hidden;
  }
  /* Front */
  .card-front {
    left: 70px;
    top: 50px;
    background: var(--brand-blue);
    color: var(--paper);
  }
  .wordmark {
    display: flex;
    align-items: center;
    gap: 12px;
    font-weight: 700;
    letter-spacing: 0.5px;
  }
  .wordmark-square {
    width: 16px;
    height: 16px;
    background: var(--accent-green);
    flex: none;
  }
  .card-front .wordmark {
    position: absolute;
    left: 0; right: 0;
    top: 120px;
    justify-content: center;
    font-size: 34px;
  }
  .card-front .web-address {
    position: absolute;
    left: 0; right: 0;
    bottom: 50px;
    text-align: center;
    font-size: 15px;
    letter-spacing: 1px;
  }
  /* Back */
  .card-back {
    left: 530px;
    top: 420px;
    background: var(--paper);
    color: var(--ink);
  }
  .wave-band {
    position: absolute;
    left: 0; top: 0;
    width: 600px;
    height: 343px;
  }
  .card-back .wordmark {
    position: absolute;
    left: 28px;
    top: 118px;
    width: 240px;
    font-size: 22px;
    line-height: 1.15;
    color: var(--brand-blue);
  }
  .divider {
    position: absolute;
    left: 288px;
    top: 40px;
    width: 2px;
    height: 178px;
    background: var(--brand-blue);
  }
  .contact {
    position: absolute;
    left: 316px;
    top: 26px;
    font-size: 14px;
    line-height: 1.3;
  }
  .contact-name {
    font-size: 23px;
    font-weight: 700;
    color: var(--brand-blue);
  }
  .contact-role { margin-bottom: 8px; }
  .contact-address { margin-bottom: 6px; }
  .contact-line {
    display: flex;
    align-items: center;
    gap: 8px;
  }
  .contact-line svg { width: 14px; height: 14px; flex: none; fill: var(--brand-blue); }
  .contact-email { font-size: 12.5px; }
  .card-back .web-address {
    position: absolute;
    left: 0; right: 0;
    bottom: 24px;
    text-align: center;
    color: var(--paper);
    font-size: 15px;
    letter-spacing: 1px;
  }
</style>
</head>
<body>

  <section class="card card-front">
    <div class="wordmark">
      <span class="wordmark-square"></span>
      <span class="wordmark-name">Velran Global Components</span>
    </div>
    <p class="web-address">www.velrancomponents-example.co.uk</p>
  </section>

  <section class="card card-back">
    <svg class="wave-band" viewBox="0 0 600 343" aria-hidden="true">
      <path d="M0,300 Q320,262 600,226 L600,240 Q320,270 0,304 Z" fill="var(--accent-green)"/>
      <path d="M0,308 Q320,276 600,246 L600,343 L0,343 Z" fill="var(--brand-blue)"/>
    </svg>

    <div class="wordmark">
      <span class="wordmark-square"></span>
      <span class="wordmark-name">Velran Global Components</span>
    </div>

    <div class="divider"></div>

    <div class="contact">
      <p class="contact-name">Rowan Ellacott</p>
      <p class="contact-role">Manager</p>
      <p class="contact-address">17 Marlow Yard, Upper Heath<br>Warwick, CV31 8QL<br>United Kingdom</p>
      <p class="contact-line">
        <svg viewBox="0 0 24 24"><path d="M6.6 10.8a15.1 15.1 0 0 0 6.6 6.6l2.2-2.2a1 1 0 0 1 1-.25 11.4 11.4 0 0 0 3.6.57 1 1 0 0 1 1 1V20a1 1 0 0 1-1 1A17 17 0 0 1 3 4a1 1 0 0 1 1-1h3.5a1 1 0 0 1 1 1c0 1.25.2 2.45.57 3.6a1 1 0 0 1-.25 1z"/></svg>
        <span>512 004 2290</span>
      </p>
      <p class="contact-line">
        <svg viewBox="0 0 24 24"><path d="M7 2h10a2 2 0 0 1 2 2v16a2 2 0 0 1-2 2H7a2 2 0 0 1-2-2V4a2 2 0 0 1 2-2zm0 3v12h10V5zm5 13.5a1 1 0 1 0 0 2 1 1 0 0 0 0-2z"/></svg>
        <span>512 004 2291</span>
      </p>
      <p class="contact-line contact-email">
        <svg viewBox="0 0 24 24"><path d="M2 5h20v14H2zm2 2v.5l8 5 8-5V7zm0 2.8V17h16V9.8l-8 5z"/></svg>
        <span>info@velrancomponents-example.co.uk</span>
      </p>
    </div>

    <p class="web-address">www.velrancomponents-example.co.uk</p>
  </section>

</body>
</html>
```